Lindqvar Foundation Letterhead

We are a newly established non profit registered in Maryland but operates in Africa, south of the sahara. We offer scholarships to deserving young adults from high school through college. Our color theme for our existing logo is purple, we want a design that is stylish, spellbinding yet a letterhead that projects seriousness. More information on www.thelindqvarfoundation.example

Target Market(s)

High school and college students in sub saharan African as well as our donors in the US

Industry/Entity Type

Non Profit

Font styles to use
Script

Requirements
Must have
• Logo at the top and if possible watermark the logo in the middle of the letterhead, contact address,
Should not have
• NA

```html
<!DOCTYPE html>
<html lang="en">
<head>
<meta charset="utf-8">
<title>Lindqvar Foundation Letterhead</title>
<link href="https://fonts.googleapis.com/css2?family=Cinzel:wght@400;600&family=Tenor+Sans&display=swap" rel="stylesheet">
<style>
  :root {
    --backdrop: #8a847c;
    --paper: #ffffff;
    --purple: #5b2a9a;
    --purple-deep: #3f1d78;
    --purple-soft: #c9b8e6;
    --ink: #2e2e2e;
    --ink-muted: #555555;
  }
  html, body {
    margin: 0;
    padding: 0;
    width: 1200px;
    height: 795px;
    overflow: hidden;
    background: var(--backdrop);
  }
  .letterhead {
    position: absolute;
    left: 320px;
    top: 16px;
    width: 540px;
    height: 763px;
    background: var(--paper);
    box-shadow: 0 4px 14px rgba(0,0,0,0.25);
    font-family: "Tenor Sans", sans-serif;
    color: var(--ink);
    overflow: hidden;
  }
  .top-band {
    height: 5px;
    background: linear-gradient(90deg, var(--purple-deep), var(--purple));
  }
  .brand {
    position: absolute;
    top: 48px;
    left: 0;
    right: 0;
    display: flex;
    flex-direction: column;
    align-items: center;
    gap: 8px;
  }
  .brand-dot {
    width: 34px;
    height: 34px;
    border-radius: 50%;
    background: var(--purple);
  }
  .brand-name {
    font-family: "Cinzel", serif;
    font-weight: 600;
    font-size: 15px;
    letter-spacing: 0.5px;
    color: var(--purple);
  }
  .side-accent {
    position: absolute;
    right: -60px;
    top: 250px;
    width: 150px;
    height: 150px;
    border-radius: 50%;
    background: var(--purple-soft);
  }
  .letter-body {
    position: absolute;
    top: 215px;
    left: 48px;
    width: 400px;
    font-size: 8.5px;
    line-height: 1.45;
  }
  .letter-body p { margin: 0 0 9px; }
  .salutation { font-size: 10px; margin-bottom: 10px !important; }
  .sign-off {
    position: absolute;
    top: 470px;
    left: 48px;
    font-size: 9px;
    color: var(--ink-muted);
  }
  .signature-mark {
    display: block;
    width: 90px;
    height: 26px;
    margin: 10px 0 4px;
    background: linear-gradient(90deg, #e6e6e6, #f4f4f4);
  }
  .sender-line { margin: 0; line-height: 1.35; }
  .contact {
    position: absolute;
    right: 36px;
    bottom: 52px;
    text-align: right;
    font-size: 8.5px;
    line-height: 1.5;
    color: var(--ink);
  }
  .contact-name {
    font-family: "Cinzel", serif;
    font-weight: 600;
    font-size: 12px;
    color: var(--purple);
    margin: 0 0 2px;
  }
  .contact p { margin: 0; }
  .label { color: var(--purple); }
</style>
</head>
<body>
  <main class="letterhead">
    <div class="top-band"></div>

    <header class="brand">
      <span class="brand-dot"></span>
      <span class="brand-name">The Lindqvar Foundation Inc</span>
    </header>

    <div class="side-accent"></div>

    <section class="letter-body">
      <p class="salutation">Dear Mr. John,</p>
      <p>Lorem Ipsum is simply dummy text of the printing and typesetting industry. Lorem Ipsum has been the industry's standard dummy text ever since the 1500s, when an unknown printer took a galley of type and scrambled it to make a type specimen book. It has survived not only five centuries, but also the leap into electronic typesetting, remaining essentially unchanged.</p>
      <p>The standard chunk of Lorem Ipsum used since the 1500s is reproduced below for those interested. Sections 1.10.32 and 1.10.33 from "de Finibus Bonorum et Malorum" by Cicero are also reproduced in their exact original form, accompanied by English versions from the 1914 translation by H. Rackham.</p>
      <p>Lorem Ipsum is simply dummy text of the printing and typesetting industry. Lorem Ipsum has been the industry's standard dummy text ever since the 1500s, when an unknown printer took a galley of type and scrambled it to make a type specimen book. It has survived not only five centuries, but also the leap into electronic typesetting, remaining essentially unchanged. It was popularised in the</p>
    </section>

    <section class="sign-off">
      <p class="sender-line">Sincerely Your,</p>
      <span class="signature-mark" role="img" aria-label="Handwritten signature"></span>
      <p class="sender-line">Name Last Name</p>
      <p class="sender-line">Company Name</p>
    </section>

    <footer class="contact">
      <p class="contact-name">The Lindqvar Foundation Inc</p>
      <p>12 Harrowfield Lane, Suite 3, Ellerton, Md 21099</p>
      <p><span class="label">email:</span> admin@thelindqvarfoundation.example <span class="label">website:</span> www.thelindqvarfoundation.example</p>
    </footer>
  </main>
</body>
</html>
```